Stationery Design Project

We need a stationery design for our Norwegian trucking company. We have existed for about 15 years and our 12 drivers uses relatively new vehicles to transport goods around in northern Norway. Long distance routes with fresh fish og food transport is our main operations.

We have already made alogo that's printed on our trucks. The logo and a picture of our trucks is attached. I think the logo i crappy, but since its already in use, changing it is not an option in this round. Still using a better colour scheme in the overall stationery and more interesting fonts is possible (altso in the logo).

Company details:
Name: Kjelvraket AS
Organisation nr 873 615 309
Post adress: 8642 Raudvik

I like minimalism and simplicity. I am avalibly for questions in normal GMT working hours either here or on mail: ivar@fjordlast.no

Reason: Hi. Im extending the deadline because I needed some time to find a vector file of our logo. Sorry for the inconvenience

Hi, and thanks for all your interest in the project. Some updates:

-          I have decided to commit to using one of the designs. Some designer will get the payment.

-          I have extended the deadline with 24 hours since I needed some time to find our firms vector logo (a slow Swedish man was holding me up)

-          We will not choose a design before the deadline. No need to rush.

-          We have received a lot of great design and think there is a need to specified the product we want to make:

o   Business Card for all our employers. I just need the design and will duplicate with the correct numbers and name myself. The information on should be: Logo, employer’s name, Phone number, email, website, Postal number and address. Use this as a template: logo, Leif Brattvoll, 47382066, Leif@fjordlast.no,, fjordlast.no, 8642 Raudvik. The order and placement of the information is your creative decision.

o   Stickers to put on the goods we travel. On the sticker the should be the following information: Logo, phone number, Tekst and link: Fraktæ av Kjelvraket. Ke du syns? Fjordlast.no/tilbakemelding (this means: Handled by Kjelvraket. What do you think Fjordlast.no/feedback -à the link will be a feedback form). The placement the information and size is your creative decision with some stings: we have been thinking of using Drukko for printing and see that a size about 6x6 cm, 8x5 or something like that. (with 3000 copies our budget is 200 punds). Any suggestions of other suppliers are welcome. Drukko price calculator http://www.drukkolabelhouse.co.uk/digital-litho-printing/printing-labels-tags/stickers/

o   Letterhead with logo, address, phone number and organizational number.

o   Envelopes with logo,address, phone number and organizational number.

Have a nice day.

 

 

• Using the blue colour in the logo and using a similar graphic approch.

```html
<!DOCTYPE html>
<html lang="no">
<head>
<meta charset="utf-8">
<title>Kjelvraket – business cards</title>
<link rel="stylesheet" href="https://fonts.googleapis.com/css2?family=Open+Sans:wght@400;600;700&display=swap">
<style>
  :root {
    --brand-dark: #0b4fa3;
    --brand-light: #0a73bb;
    --ink: #2b2b2b;
    --paper: #ffffff;
    --backdrop: #d9dbde;
    --edge: #1c1c1c;
  }
  * { box-sizing: border-box; margin: 0; padding: 0; }
  html, body { width: 1200px; height: 751px; overflow: hidden; }
  body {
    background: var(--backdrop);
    font-family: "Open Sans", sans-serif;
    position: relative;
  }
  .card {
    position: absolute;
    width: 524px;
    height: 298px;
    border-radius: 18px;
    overflow: hidden;
  }
  .card--front { left: 64px; top: 52px; background: var(--paper); }
  .card--navy  { left: 620px; top: 52px; background: var(--brand-dark); }
  .card--white { left: 64px; top: 393px; background: var(--paper); border: 1px solid var(--edge); }
  .card--sky   { left: 620px; top: 393px; background: var(--brand-light); }

  .wordmark {
    position: absolute;
    left: 0; right: 0;
    display: flex;
    justify-content: center;
    align-items: center;
    gap: 12px;
    font-weight: 700;
    font-size: 46px;
    letter-spacing: -0.5px;
    color: var(--brand-dark);
  }
  .wordmark__dot {
    width: 26px; height: 26px; border-radius: 50%;
    background: currentColor;
  }
  .card--front .wordmark { top: 48px; }
  .card--navy .wordmark,
  .card--sky .wordmark { top: 118px; color: var(--paper); }
  .card--white .wordmark { top: 118px; }

  .website {
    position: absolute;
    left: 0; right: 0;
    text-align: center;
    font-size: 17px;
    letter-spacing: 3.5px;
  }
  .card--front .website { bottom: 7px; font-size: 13px; letter-spacing: 2.5px; color: var(--paper); }
  .card--navy .website, .card--sky .website { bottom: 28px; color: var(--paper); }
  .card--white .website { bottom: 28px; color: var(--ink); }

  .wave { position: absolute; left: 0; top: 0; }

  .person {
    position: absolute;
    right: 286px;
    top: 162px;
    text-align: right;
  }
  .person__name { font-size: 19px; font-weight: 700; color: var(--brand-dark); line-height: 1.2; }
  .person__address { font-size: 15px; color: var(--ink); margin-top: 4px; display: flex; align-items: center; justify-content: flex-end; gap: 6px; }

  .divider {
    position: absolute;
    left: 253px; top: 150px;
    width: 1px; height: 70px;
    background: #9a9a9a;
  }
  .contact {
    position: absolute;
    left: 265px; top: 153px;
    list-style: none;
    font-size: 15px;
    color: var(--ink);
    line-height: 22.5px;
  }
  .contact li { display: flex; align-items: center; gap: 5px; }
  .contact__label { color: var(--brand-light); }
  .icon { width: 11px; height: 11px; fill: var(--brand-light); }
</style>
</head>
<body>

<section class="card card--front">
  <svg class="wave" width="524" height="298" viewBox="0 0 524 298" aria-hidden="true">
    <path d="M0 190 Q250 285 524 240 L524 298 L0 298 Z" fill="var(--brand-dark)"/>
    <path d="M0 207 Q240 290 440 262" fill="none" stroke="var(--paper)" stroke-width="3"/>
  </svg>

  <div class="wordmark"><span>Kjelvraket</span><span class="wordmark__dot"></span></div>

  <div class="person">
    <p class="person__name">Leif Brattvoll</p>
    <p class="person__address">
      <svg class="icon" viewBox="0 0 12 12" aria-hidden="true"><path d="M6 1 L11 5 L11 11 L1 11 L1 5 Z"/></svg>
      8642 Raudvik
    </p>
  </div>

  <div class="divider"></div>

  <ul class="contact">
    <li>
      <svg class="icon" viewBox="0 0 12 12" aria-hidden="true"><path d="M3 1 L5 3.5 L4 5 Q5.5 7.5 7 8 L8.5 7 L11 9 L9.5 11 Q4 10.5 1 3 Z"/></svg>
      47382066
    </li>
    <li><span class="contact__label">Org nr</span> 873 615 309</li>
    <li>
      <svg class="icon" viewBox="0 0 12 12" aria-hidden="true"><path d="M1 4 L6 1 L11 4 L11 11 L1 11 Z"/></svg>
      Leif@fjordlast.no
    </li>
  </ul>

  <p class="website">www.fjordlast.no</p>
</section>

<section class="card card--navy">
  <div class="wordmark"><span>Kjelvraket</span><span class="wordmark__dot"></span></div>
  <p class="website">www.fjordlast.no</p>
</section>

<section class="card card--white">
  <div class="wordmark"><span>Kjelvraket</span><span class="wordmark__dot"></span></div>
  <p class="website">www.fjordlast.no</p>
</section>

<section class="card card--sky">
  <div class="wordmark"><span>Kjelvraket</span><span class="wordmark__dot"></span></div>
  <p class="website">www.fjordlast.no</p>
</section>

</body>
</html>
```